New Webpage for High Class Expert Witness Services Company

We are looking for a minimalist design for a webpage that just has our logo and an entry form offer to connect with one of our Liaisons.
The entry form should just ask for Name, Email, Contact Info and Description of Project.

Company Name is: The Marlowe Crest Advisory Services

Number of Pages Required

1 page

```html
<!DOCTYPE html>
<html lang="en">
<head>
<meta charset="UTF-8">
<title>Marlowe Crest Advisory Services</title>
<link href="https://fonts.googleapis.com/css2?family=Cinzel:wght@400;700&family=Montserrat:wght@400;500&display=swap" rel="stylesheet">
<style>
  :root {
    --bg-deep: #0a0a0a;
    --bg-soft: #1c1c1c;
    --silver: #d9d9db;
    --silver-dim: #a9a9ad;
    --text: #f2f2f2;
    --field-border: #3a3a3c;
    --card-border: #4a4a4c;
    --rule: #2c2c2e;
  }
  * { margin: 0; padding: 0; box-sizing: border-box; }
  html, body { width: 862px; height: 1200px; overflow: hidden; }
  body {
    position: relative;
    background:
      radial-gradient(ellipse 420px 260px at 780px 260px, rgba(255,255,255,0.07), transparent 70%),
      radial-gradient(ellipse 300px 120px at 40px 520px, rgba(255,255,255,0.06), transparent 70%),
      linear-gradient(160deg, var(--bg-soft) 0%, var(--bg-deep) 45%, #111 75%, var(--bg-soft) 100%);
    color: var(--text);
    font-family: "Montserrat", sans-serif;
  }
  .brand {
    position: absolute; left: 147px; top: 55px; width: 568px;
    text-align: center; font-family: "Cinzel", serif; font-weight: 400; color: var(--silver);
  }
  .brand-name { font-size: 44px; line-height: 52px; letter-spacing: 2px; }
  .brand-sub { font-size: 21px; line-height: 34px; letter-spacing: 8px; }
  .hero-title {
    position: absolute; left: 0; top: 202px; width: 862px; text-align: center;
    font-family: "Cinzel", serif; font-weight: 700; font-size: 34px; line-height: 40px;
    color: var(--silver);
  }
  .hero-rule { position: absolute; left: 366px; top: 295px; width: 130px; height: 2px; background: var(--silver); }
  .hero-lead {
    position: absolute; left: 0; top: 320px; width: 862px; text-align: center;
    font-size: 18px; line-height: 22px; color: var(--text);
  }
  .consult-card {
    position: absolute; left: 105px; top: 400px; width: 652px; height: 435px;
    border: 1px solid var(--card-border); border-radius: 12px;
    background: linear-gradient(170deg, #222 0%, #080808 55%, #151515 100%);
    box-shadow: 0 10px 30px rgba(0,0,0,0.6);
    padding: 37px 32px 0;
  }
  .field {
    height: 60px; margin-bottom: 10px; border: 1px solid var(--field-border); border-radius: 6px;
    padding-left: 29px; display: flex; align-items: center;
    font-size: 12.5px; font-weight: 500; color: var(--text);
    background: rgba(0,0,0,0.15);
  }
  .field-area { height: 91px; align-items: flex-start; padding-top: 22px; }
  .submit-btn {
    display: block; margin: 24px auto 0; width: 166px; height: 34px;
    border: none; border-radius: 4px;
    background: linear-gradient(#f0f0f0, #b9b9bc);
    font-family: "Montserrat", sans-serif; font-size: 12.5px; font-weight: 500; color: #111;
  }
  .emblem-area {
    position: absolute; left: 112px; top: 897px; width: 190px; height: 225px;
    background: linear-gradient(#e6e6e8, #8e8e92); opacity: 0.15; border-radius: 4px;
  }
  .about-title {
    position: absolute; left: 400px; top: 897px;
    font-family: "Cinzel", serif; font-weight: 700; font-size: 31px; line-height: 40px; color: var(--silver);
  }
  .about-rule { position: absolute; left: 401px; top: 942px; width: 105px; height: 2px; background: var(--silver); }
  .about-copy {
    position: absolute; left: 401px; top: 968px; width: 381px;
    font-size: 11px; line-height: 18.5px; text-align: justify; color: var(--text);
  }
  .about-copy p + p { margin-top: 17px; }
  .site-footer {
    position: absolute; left: 20px; top: 1164px; width: 822px; height: 36px;
    border-top: 1px solid var(--rule); text-align: center;
    font-size: 10.5px; line-height: 36px; color: #cfcfcf;
  }
</style>
</head>
<body>
  <header class="brand">
    <div class="brand-name">MARLOWE CREST</div>
    <div class="brand-sub">ADVISORY SERVICES</div>
  </header>

  <h1 class="hero-title">GET CONNECTED WITH AN EXPERT<br>WITNESS LIAISON</h1>
  <div class="hero-rule"></div>
  <p class="hero-lead">Connecting you with vetted medical experts—accurately, efficiently,<br>and with complete confidentiality.</p>

  <form class="consult-card">
    <div class="field">Name</div>
    <div class="field">Email</div>
    <div class="field">Contact Info</div>
    <div class="field field-area">Description of Project.</div>
    <button class="submit-btn" type="button">Request Consultation</button>
  </form>

  <section>
    <div class="emblem-area" role="img" aria-label="Large brand emblem area"></div>
    <h2 class="about-title">ABOUT US</h2>
    <div class="about-rule"></div>
    <div class="about-copy">
      <p>The Marlowe Crest Advisory Services provides seamless access to highly qualified medical expert witnesses for legal professionals. We specialize in connecting attorneys with vetted experts who deliver clarity, credibility, and precision in complex cases.</p>
      <p>Our approach is defined by discretion, efficiency, and an uncompromising standard of professionalism—ensuring every engagement is handled with care and confidence.</p>
    </div>
  </section>

  <footer class="site-footer">Copyright © 2026 MARLOWE CREST. All rights reserved.</footer>
</body>
</html>
```